Redesign This Psychology Website

We would like a slight redesign of this successful psychology (relationship counselling) website:

www.TheKelvaleClinic.com.au

We are updating the website, and we'd like a slight refresh of the design and style.

Please keep to very similar colours, and use the same logo. We're looking for around 10 page templates, however the main one is the home page.

Keep in mind, this website already converts quite well, so we want a new, fresh design in keeping with this one. Please don't bother designing something too extremely different.

thanks :)

Target Market(s)

couples who are looking for relationship counselling. Men and women, 25 - 70, across Australia

Industry/Entity Type

Psychology

Number of Pages Required

5+ page

Font styles to use
Sans Serif

Colors
87cfc6
b7a5cd
ec1f27
ffffff
cee9f5

Requirements
Must have
• a similar look to the current design, just looking for a slight refresh.
• Search bar
• Areas for lots of photos
• same logo
• lots of content areas
Nice to have
• great content areas, where we can display a lot of content and our areas.
Should not have
• no colors like orange, etc.
• should not have a totally different feel.

```html
<!DOCTYPE html>
<html lang="en">
<head>
<meta charset="utf-8">
<title>The Kelvale Clinic – Shop</title>
<link rel="stylesheet" href="https://fonts.googleapis.com/css2?family=Mulish:wght@400;600;700&display=swap">
<style>
:root{
  --teal:#1a7f8c;
  --teal-light:#87cfc6;
  --teal-soft:#a6ddd6;
  --red:#ec1f27;
  --ink:#333;
  --muted:#666;
  --line:#dcdcdc;
  --bar:#f2f2f2;
  --white:#fff;
}
*{box-sizing:border-box;margin:0;padding:0}
html,body{width:1010px;height:1200px;overflow:hidden;background:var(--white);font-family:"Mulish",sans-serif;color:var(--ink)}
.page{position:relative;width:1010px;height:1200px}
.topbar{height:31px;background:var(--bar);border-bottom:1px solid var(--line);display:flex;align-items:center;justify-content:space-between;padding:0 130px 0 111px;font-size:12.5px;color:var(--muted)}
.topbar__links{display:flex;height:31px}
.topbar__links span{padding:0 9px;display:flex;align-items:center;border-right:1px solid var(--line)}
.topbar__links span:last-child{border-right:0}
.header{height:105px;display:flex;align-items:center;padding:0 110px 0 98px}
.brand{display:flex;align-items:center;gap:8px;width:286px}
.brand__dot{width:40px;height:40px;border-radius:50%;background:var(--teal);flex:none}
.brand__name{font-size:27px;color:var(--teal);font-weight:400;line-height:1}
.brand__tag{font-size:11.5px;color:var(--teal);margin-top:4px}
.search{width:300px;height:34px;border:1px solid var(--line);display:flex;align-items:center;gap:7px;padding:0 10px;font-size:12px;color:#999;margin-left:0}
.call{margin-left:auto;text-align:right}
.call__label{font-size:15px;color:var(--teal-light)}
.call__number{font-size:20px;font-weight:700;color:var(--teal);display:flex;align-items:center;gap:6px}
.nav{height:56px;background:linear-gradient(#9fdad2,#7cc6bd);display:flex;padding-left:94px}
.nav a{display:flex;align-items:center;padding:0 9px;color:var(--white);font-size:14px;font-weight:600;text-transform:uppercase;line-height:1.05;text-decoration:none;border-right:1px solid rgba(255,255,255,.45)}
.nav a:last-child{border-right:0}
.hero{position:relative;height:274px;background:linear-gradient(100deg,#c9b8a6 0%,#8a6e5a 35%,#b58c78 60%,#d8cfc4 100%)}
.hero__title{position:absolute;left:107px;top:133px;font-size:30px;font-weight:700;color:var(--white);letter-spacing:.5px}
.shop{padding:50px 0 0 114px}
.shop__title{font-size:25px;font-weight:400}
.shop__count{font-size:15px;color:var(--muted);margin-top:6px}
.products{display:flex;gap:5px;margin:18px 0 0 -4px}
.card{width:191px;height:240px;border:1px solid var(--line);padding:30px 8px 0 13px}
.card__image{height:140px;width:90px;margin:0 auto 0 40px}
.card__name{margin-top:26px;font-size:13px}
.card__row{display:flex;justify-content:space-between;align-items:center;margin-top:2px}
.card__price{color:var(--teal);font-size:15px}
.card__btn{background:var(--red);color:var(--white);font-size:10px;font-weight:700;width:80px;height:22px;display:flex;align-items:center;justify-content:center}
.footer{position:absolute;top:886px;left:0;width:1010px;height:252px;background:linear-gradient(#ececec,#fff 50px)}
.footer .brand{position:absolute;left:121px;top:70px}
.footer__col{position:absolute;top:62px;font-size:11px;color:var(--muted)}
.footer__col h3{font-size:14px;color:var(--teal);font-weight:600;margin-bottom:6px;text-transform:uppercase}
.footer__col p{line-height:23px}
.social{display:flex;gap:5px;margin-top:8px}
.social span{width:28px;height:28px;border-radius:50%}
.copyright{position:absolute;top:1138px;left:0;width:1010px;height:62px;background:var(--bar);display:flex;align-items:center;justify-content:center;font-size:10.5px;color:var(--muted)}
</style>
</head>
<body>
<div class="page">
  <div class="topbar">
    <span>Join Our Associate Program →</span>
    <div class="topbar__links"><span>Home</span><span>Cart</span><span>Blog</span><span>Resources</span><span>Contact</span></div>
  </div>

  <header class="header">
    <div class="brand">
      <span class="brand__dot"></span>
      <div><div class="brand__name">The Kelvale Clinic</div><div class="brand__tag">helping you create loving relationships</div></div>
    </div>
    <div class="search">
      <svg width="13" height="13" viewBox="0 0 13 13"><circle cx="5.5" cy="5.5" r="4.5" fill="none" stroke="#bbb" stroke-width="1.4"/><line x1="9" y1="9" x2="12" y2="12" stroke="#bbb" stroke-width="1.4"/></svg>
      Search here
    </div>
    <div class="call">
      <div class="call__label">Call Us Now</div>
      <div class="call__number">
        <svg width="20" height="20" viewBox="0 0 24 24"><path d="M6 2l4 4-2 3c1.5 3 4 5.5 7 7l3-2 4 4-3 3C10 20 4 14 2 5z" fill="none" stroke="#ec1f27" stroke-width="1.6" stroke-linejoin="round"/></svg>
        1300 555 017
      </div>
    </div>
  </header>

  <nav class="nav">
    <a>Counselling<br>Types</a>
    <a>Relationship Counselling<br>Locations</a>
    <a>Sex Therapy<br>Locations</a>
    <a>About Us</a>
    <a>Quizzes</a>
    <a style="padding:0 16px">FAQ’s</a>
    <a>Contact</a>
  </nav>

  <section class="hero" role="img" aria-label="Photo of a smiling couple looking at a laptop together in a cafe">
    <div class="hero__title">SHOP NOW</div>
  </section>

  <section class="shop">
    <h1 class="shop__title">Shop</h1>
    <p class="shop__count">Showing the single result</p>
    <div class="products">
      <div class="card">
        <div class="card__image" role="img" aria-label="Book cover with a couple embracing" style="background:linear-gradient(#e7c9a5,#c98d6d 70%,#d8306a)"></div>
        <div class="card__name">Evenings Together</div>
        <div class="card__row"><span class="card__price">$9.95</span><span class="card__btn">Add to Cart</span></div>
      </div>
      <div class="card">
        <div class="card__image" role="img" aria-label="Black book case with a disc" style="width:120px;margin-left:32px;background:linear-gradient(90deg,#2a2a2a,#444 60%,#888)"></div>
        <div class="card__name">Evenings Together</div>
        <div class="card__row"><span class="card__price">$9.95</span><span class="card__btn">Add to Cart</span></div>
      </div>
      <div class="card">
        <div class="card__image" role="img" aria-label="Plain white product box" style="width:80px;margin-left:50px;background:linear-gradient(90deg,#f4f4f4,#e2e2e2)"></div>
        <div class="card__name">Evenings Together</div>
        <div class="card__row"><span class="card__price">$9.95</span><span class="card__btn">Add to Cart</span></div>
      </div>
      <div class="card">
        <div class="card__image" role="img" aria-label="Light blue DVD case" style="width:74px;margin-left:48px;background:#dbe9f1;border:3px solid #444"></div>
        <div class="card__name">Evenings Together</div>
        <div class="card__row"><span class="card__price">$9.95</span><span class="card__btn">Add to Cart</span></div>
      </div>
    </div>
  </section>

  <footer class="footer">
    <div class="brand">
      <span class="brand__dot"></span>
      <div><div class="brand__name">The Kelvale Clinic</div><div class="brand__tag">helping you create loving relationships</div></div>
    </div>
    <div class="footer__col" style="left:392px">
      <h3>Quick Links</h3>
      <p>Home</p><p>About Us</p><p>Our Blogs</p><p>Shop Cart</p><p>Contact Us</p>
    </div>
    <div class="footer__col" style="left:533px">
      <h3>Resources</h3>
      <p>Counselling Type</p><p>Sex Therapy</p><p>Quizzes</p><p>FAQ</p><p>Relationship Counselling</p>
    </div>
    <div class="footer__col" style="left:705px;font-size:10px">
      <h3>Contact Us</h3>
      <p>42 Harbour Lane Suite 7</p><p>1300 555 017</p><p>Email: hello@kelvaleclinic.com.au</p>
      <div class="social"><span style="background:#4fb3e6"></span><span style="background:#2a5bb0"></span><span style="background:#1a7f8c"></span><span style="background:#e0453a"></span></div>
    </div>
  </footer>

  <div class="copyright">© 2017 Company Name &nbsp;All right reserved</div>
</div>
</body>
</html>
```